Killer Webpage Design

I currently have a self-hosted webpage through wordpress at www.velmarqstudio.com - the content is complete and I'm happy with this but I need it designed (no coding) to complete my requirements. I'm happy to take designs which are non-Wordpress if there is specific advantage in this.

My full branding logos are attached along with color files. My main aim is consistent branding across all areas (social media, business cards, emails, websites). I have the rest running but am not happy with the available default selections from Wordpress.

I would prefer to use the darker blue version of the logo as I feel this has more standout in online media, however I would appreciate submissions with both variants to help me choose.

With the homepage I will also want to see blog pages and category pages designed but this can come after I have selected a design to go with,

Sites that I like and are related to my business include the following:
http://www.brindlepath.com/au/accounting-software/
http://www.tasklanternpro.com/home.aspx
https://pelicoin.com/register
Updates

Apologies for the confusion - to clarify for designers I am looking for design only, no coding.

FYI - i have now uploaded business cards for an idea of the contemporary style of design completed so far.

Target Market(s)

small to medium business. Not systemised but looking for help and support.

Industry/Entity Type

Business

Requirements
Must have
• I'm looking for a minimalist professional page, with the ability to easily add new sections when required. I will also need a CMS to add blog posts on the go, with the same features that it currently has (comments, social logon etc)

```html
<!DOCTYPE html>
<html lang="en">
<head>
<meta charset="utf-8">
<title>Velmarq Studio</title>
<link rel="stylesheet" href="https://fonts.googleapis.com/css2?family=Ubuntu:wght@400;500;700&display=swap">
<style>
:root{
  --header:#04202e;
  --nav:#33b5c9;
  --nav-dark:#1e8ea2;
  --nav-line:#1f98ad;
  --teal-text:#1e6b84;
  --blog-red:#a3262a;
  --side-orange:#c9561c;
  --body-text:#333;
  --page-bg:#f0f0f0;
  --card-bg:#e8e8e8;
  --card-line:#d6d6d6;
  --footer:#2e2e2e;
  --footer-text:#dcdcdc;
}
*{margin:0;padding:0;box-sizing:border-box}
html,body{width:874px;height:1200px;overflow:hidden}
body{position:relative;font-family:"Ubuntu",sans-serif;background:var(--page-bg);color:var(--body-text)}
.site-header{position:absolute;left:0;top:0;width:874px;height:87px;background:linear-gradient(#022030,#06283a)}
.brand{position:absolute;left:74px;top:22px;display:flex;align-items:center;gap:10px}
.brand-dot{width:34px;height:34px;border-radius:50%;background:#2aa6b8}
.brand-name{font-size:25px;font-weight:500;color:#fff}
.search{position:absolute;left:587px;top:32px;width:153px;height:22px;background:#fff;font-size:10px;color:#666;padding:5px 12px}
.search svg{position:absolute;right:7px;top:5px}
.lang{position:absolute;left:747px;top:32px;width:62px;height:22px;background:#fff;font-size:10px;color:#555;padding:5px 0 0 8px}
.lang .flag{display:inline-block;width:12px;height:8px;background:#4b5f9c;margin-right:4px;vertical-align:0}
.lang svg{position:absolute;right:7px;top:9px}
.main-nav{position:absolute;left:0;top:87px;width:874px;height:39px;background:linear-gradient(#42c3d6,#2aa9be);display:flex;padding-left:66px}
.main-nav a{color:#fff;font-size:11.5px;text-decoration:none;padding:13px 11px 0;border-right:1px solid var(--nav-line);height:39px}
.main-nav a.active{background:var(--nav-dark);padding:13px 14px 0}
.hero{position:absolute;left:0;top:126px;width:874px;height:229px}
.hero-image{position:absolute;inset:0;background:linear-gradient(180deg,#7fb0d2 0%,#b3cfe3 60%,#e3ebf1 100%)}
.hero-panel{position:absolute;left:394px;top:32px;width:415px;height:172px;background:rgba(35,50,62,.78);padding:15px 29px;color:#fff}
.hero-panel h1{font-size:18.5px;font-weight:700;line-height:26px}
.hero-panel p{font-size:10.5px;line-height:17px;margin-top:10px}
.demo-btn{position:absolute;left:29px;top:118px;width:121px;height:32px;background:#fff;color:#333;font-size:15px;padding:7px 0 0 9px;border-radius:2px}
.demo-btn svg{position:absolute;right:9px;top:8px}
.section-title{position:absolute;font-size:18px;font-weight:500}
.blog-title{left:66px;top:373px;color:var(--blog-red)}
.post{position:absolute;left:66px;width:512px;height:131px}
.post-image{position:absolute;left:0;top:0;width:149px;height:131px}
.post-body{position:absolute;left:168px;top:-3px;width:344px}
.post-body h2{font-size:13px;font-weight:400;color:var(--teal-text)}
.post-date{font-size:9.5px;margin-top:4px}
.post-body p{font-size:10px;line-height:16.5px;text-align:justify;margin-top:8px}
.share{display:flex;gap:3px;margin-top:8px;font-size:8px}
.share span{border:1px solid #c8c8c8;background:#f7f7f7;padding:1px 3px;border-radius:2px}
.share .btn{color:#334;font-weight:500}
.share .btn::before{content:"";display:inline-block;width:7px;height:7px;background:#4a6aa8;margin-right:3px;vertical-align:-1px}
.share .btn.tw::before{background:#3aa0d8}
.share .count{margin-right:6px}
.pager{position:absolute;left:371px;top:1053px;display:flex;gap:3px;font-size:7px;color:#999}
.pager span{width:16px;height:16px;background:#d0d0d0;border-radius:2px;text-align:center;padding-top:4px}
.pager span.current{background:#8d8d8d;color:#fff}
.pager .gap{background:none;width:10px}
.side-title{left:602px;color:var(--side-orange)}
.card{position:absolute;left:602px;width:207px;height:100px;background:var(--card-bg);border:1px solid var(--card-line)}
.card-image{position:absolute;left:9px;top:10px;width:77px;height:80px}
.card-text{position:absolute;left:96px;top:12px;width:103px;font-size:11.5px;line-height:16.5px;color:var(--teal-text);text-align:justify}
.card-date{position:absolute;left:96px;top:70px;font-size:9.5px;color:#333}
.site-footer{position:absolute;left:0;top:1118px;width:874px;height:82px;background:var(--footer);color:var(--footer-text);font-size:10.5px}
.footer-nav{position:absolute;left:66px;top:22px}
.footer-nav a{color:var(--footer-text);text-decoration:none}
.footer-nav i{font-style:normal;margin:0 8px}
.copyright{position:absolute;left:66px;top:49px}
.social{position:absolute;left:768px;top:33px;display:flex;gap:4px}
.social span{width:18px;height:18px;border-radius:3px;background:#3d5f9e}
.social span+span{background:#3fa3d6}
</style>
</head>
<body>
<header class="site-header">
  <div class="brand"><span class="brand-dot"></span><span class="brand-name">Velmarq Studio</span></div>
  <div class="search">Search<svg width="11" height="11" viewBox="0 0 11 11"><circle cx="4.5" cy="4.5" r="3.3" fill="none" stroke="#222" stroke-width="1.6"/><line x1="7" y1="7" x2="10" y2="10" stroke="#222" stroke-width="2"/></svg></div>
  <div class="lang"><span class="flag"></span>Eng<svg width="7" height="4" viewBox="0 0 7 4"><path d="M0 0h7L3.5 4z" fill="#444"/></svg></div>
</header>
<nav class="main-nav">
  <a class="active" href="#">Home</a>
  <a href="#">Software Training and Implementation</a>
  <a href="#">Project Management</a>
  <a href="#">Business Process Analysis</a>
  <a href="#">Blog</a>
  <a href="#">About Us</a>
  <a href="#">Contact Us</a>
</nav>
<section class="hero">
  <div class="hero-image" role="img" aria-label="Photo of a glass globe on a pedestal against a cloudy blue sky"></div>
  <div class="hero-panel">
    <h1>Curabitur non massa vestibulum, egestas velit vitae, imperdiet velit.</h1>
    <p>Aliquam interdum sollicitudin odio. Mauris nunc ante, sagittis id porta quis, semper non neque. Suspendisse ac pulvinar tellus.</p>
    <div class="demo-btn"><b>FREE</b> Demo<svg width="16" height="16" viewBox="0 0 16 16"><circle cx="8" cy="8" r="8" fill="#666"/><path d="M6.5 4.5L10 8l-3.5 3.5" fill="none" stroke="#fff" stroke-width="1.8"/></svg></div>
  </div>
</section>

<h2 class="section-title blog-title">Blog</h2>

<article class="post" style="top:411px">
  <div class="post-image" role="img" aria-label="Cloud icon above a glowing circuit board" style="background:linear-gradient(135deg,#0a1f7a,#1e5fd8 55%,#0b1c6a)"></div>
  <div class="post-body">
    <h2>Atullam volutpat dui et nisl pharetra, in convallis ipsum</h2>
    <div class="post-date">July-31-13 &nbsp;::&nbsp; 10.15 a.m</div>
    <p>Pellentesque at tristique nunc. Nunc quam orci, egestas et tortor et, molestie adipiscing velit. Nunc hen drerit risus ut dui condimentum dignis-sim. Sed nec mattis augue. Nunc ante eros, eleifend ac odio id, dictum sagittis urna. Praesent eros dolor, condimentum ac laoreet id.</p>
    <div class="share"><span class="btn">Like</span><span class="count">3k</span><span class="btn tw">Tweet</span><span>316</span></div>
  </div>
</article>
<article class="post" style="top:571px">
  <div class="post-image" role="img" aria-label="Corridor of server racks lit in blue" style="background:linear-gradient(90deg,#0b1a5a,#3f6fd8 50%,#0b1a5a)"></div>
  <div class="post-body">
    <h2>Atullam volutpat dui et nisl pharetra, in convallis ipsum</h2>
    <div class="post-date">July-31-13 &nbsp;::&nbsp; 10.15 a.m</div>
    <p>Pellentesque at tristique nunc. Nunc quam orci, egestas et tortor et, molestie adipiscing velit. Nunc hen drerit risus ut dui condimentum dignis-sim. Sed nec mattis augue. Nunc ante eros, eleifend ac odio id, dictum sagittis urna. Praesent eros dolor, condimentum ac laoreet id.</p>
    <div class="share"><span class="btn">Like</span><span class="count">3k</span><span class="btn tw">Tweet</span><span>316</span></div>
  </div>
</article>
<article class="post" style="top:730px">
  <div class="post-image" role="img" aria-label="Hand touching floating screens in a blue sky" style="background:linear-gradient(160deg,#3f8fdc,#bcdaf2 60%,#e8eef2)"></div>
  <div class="post-body">
    <h2>Atullam volutpat dui et nisl pharetra, in convallis ipsum</h2>
    <div class="post-date">July-31-13 &nbsp;::&nbsp; 10.15 a.m</div>
    <p>Pellentesque at tristique nunc. Nunc quam orci, egestas et tortor et, molestie adipiscing velit. Nunc hen drerit risus ut dui condimentum dignis-sim. Sed nec mattis augue. Nunc ante eros, eleifend ac odio id, dictum sagittis urna. Praesent eros dolor, condimentum ac laoreet id.</p>
    <div class="share"><span class="btn">Like</span><span class="count">3k</span><span class="btn tw">Tweet</span><span>316</span></div>
  </div>
</article>
<article class="post" style="top:890px">
  <div class="post-image" role="img" aria-label="Illustrated business people standing on a white cloud" style="background:linear-gradient(180deg,#eef2f6,#dfe6ec)"></div>
  <div class="post-body">
    <h2>Atullam volutpat dui et nisl pharetra, in convallis ipsum</h2>
    <div class="post-date">July-31-13 &nbsp;::&nbsp; 10.15 a.m</div>
    <p>Pellentesque at tristique nunc. Nunc quam orci, egestas et tortor et, molestie adipiscing velit. Nunc hen drerit risus ut dui condimentum dignis-sim. Sed nec mattis augue. Nunc ante eros, eleifend ac odio id, dictum sagittis urna. Praesent eros dolor, condimentum ac laoreet id.</p>
    <div class="share"><span class="btn">Like</span><span class="count">3k</span><span class="btn tw">Tweet</span><span>316</span></div>
  </div>
</article>

<div class="pager"><span class="current">1</span><span>2</span><span>3</span><span>4</span><span>5</span><span>6</span><span>7</span><span>8</span><span>»</span><span class="gap">…</span><span>»»</span></div>

<h2 class="section-title side-title" style="top:385px">Popular Post</h2>
<div class="card" style="top:412px"><div class="card-image" role="img" aria-label="Digital cloud on a blue background" style="background:linear-gradient(135deg,#1a7fd8,#5fb7ee)"></div><div class="card-text">Mauris aptet neque quis pretium eifend dictum</div><div class="card-date">July-31-13 &nbsp;::&nbsp; 10.15 a.m</div></div>
<div class="card" style="top:516px"><div class="card-image" role="img" aria-label="White 3D figure reading a newspaper in a chair" style="background:linear-gradient(180deg,#fafafa,#d9d9d9)"></div><div class="card-text">Mauris aptet neque quis pretium eifend dictum</div><div class="card-date">July-31-13 &nbsp;::&nbsp; 10.15 a.m</div></div>
<div class="card" style="top:620px"><div class="card-image" role="img" aria-label="Businessman with laptop in front of office towers" style="background:linear-gradient(180deg,#4f8fd2,#c9dcec)"></div><div class="card-text">Mauris aptet neque quis pretium eifend dictum</div><div class="card-date">July-31-13 &nbsp;::&nbsp; 10.15 a.m</div></div>

<h2 class="section-title side-title" style="top:742px">Older Post</h2>
<div class="card" style="top:770px"><div class="card-image" role="img" aria-label="Finger touching a tablet screen" style="background:linear-gradient(135deg,#12306e,#3a78c8 60%,#d8a888)"></div><div class="card-text">Mauris aptet neque quis pretium eifend dictum</div><div class="card-date">July-31-13 &nbsp;::&nbsp; 10.15 a.m</div></div>
<div class="card" style="top:874px"><div class="card-image" role="img" aria-label="Cloud with tablet and phone" style="background:linear-gradient(180deg,#ffffff,#cfe4f3)"></div><div class="card-text">Mauris aptet neque quis pretium eifend dictum</div><div class="card-date">July-31-13 &nbsp;::&nbsp; 10.15 a.m</div></div>
<div class="card" style="top:978px"><div class="card-image" role="img" aria-label="Businessman pointing at a network of people icons" style="background:linear-gradient(135deg,#c9e2f3,#6ea6d6)"></div><div class="card-text">Mauris aptet neque quis pretium eifend dictum</div><div class="card-date">July-31-13 &nbsp;::&nbsp; 10.15 a.m</div></div>

<footer class="site-footer">
  <div class="footer-nav"><a href="#">Home</a><i>|</i><a href="#">Software Training and Implementation</a><i>|</i><a href="#">Project Management</a><i>|</i><a href="#">Business Process Analysis</a><i>|</i><a href="#">Blog</a><i>|</i><a href="#">About Us</a><i>|</i><a href="#">Contact Us</a></div>
  <div class="copyright">Copyright &nbsp;©&nbsp; 2013 &nbsp; Velmarq Studio. &nbsp; All rights reserved.</div>
  <div class="social"><span></span><span></span></div>
</footer>
</body>
</html>
```